Corwin Beacon Lighting - Commercial & Residential Landscape Lighting

Landscape Lighting Services & Design: Create a website for our landscape lighting company. We would like the design to be tailored around this description:
Illuminate with Confidence. Designed with Precision. Installed with Care.
Locally and veteran-owned, we take pride in transforming outdoor spaces through innovative lighting solutions tailored to your vision. From landscape and holiday lighting to permanent installations, our effortless process and expert design deliver breathtaking results and lasting curb appeal. Backed by a lifetime warranty and quarterly service options, our commitment to quality and customer satisfaction is unwavering. Try before you buy and experience your home in a whole new light with our complimentary demo kit — see the stunning effects before you decide.
- Also, add in this information as well; Outdoor Lighting not only beautifies spaces but also significantly enhances safety by illuminating your home or business. Beautifully lit entrances deter potential intruders, making your home a safer place for your loved ones. we also offer quarterly service plans to ensure lighting equipment continues to operate & illuminate effectively throughout the year. Also mention we provide free estimates and we are offering a 10% discount to military, veterans, and first responders.

Target Market(s)

Luxury market

Industry/Entity Type

Landscape Lighting - Residential & Commercial Lighting Services

Coding

Coded - Design and coding required

Number of Pages Required

2 page

Colors
00AB8E
00BBA5
67D7C9
C6EFE9
E9F9F6
59FF00
82FF00
B8FF75
E3FFCB
F4FFEA
FFC000
F8CF3A
FAE287
FDF2CF
FEFAEE

Requirements
Must have
• a lead generation button where people can submit their information for us to reach out to them and schedule their free estimate, homepage, about page, contact page, products and services page, user friendly, easy to navigate, and it also must be engaging and eye popping, as well as appealing to the luxury market. Please use colors; verdent green, dark green, ivory, and sunny yellow. Also, include an about page that references our story; Derek is retired Army and he opened a fitness studio in 2017 with his wife Jolene. He has installed low voltage lighting in every home he lived in and for his friends and family over the years and decided to open his own business because he is passionate about beautifying outdoor landscapes and highlighting a properties full potential, not only in the day but at night as well all while providing safety and security for his clients. Having a deep respect for nature and landscaping, he wants to provide the same care and quality to each of his clients as he has in the fitness industry for decades. He believes small businesses are the back bone of America and he's excited to provide a service that is all to often neglected in the design of a home.
Nice to have
• I would like to have a clear intent and purpose, engaging web design, clear call to action, optimized for search engines, mobile friendy design, security measures, credibility indicators

```html
<!DOCTYPE html>
<html lang="en">
<head>
<meta charset="utf-8">
<title>Corwin Beacon Lighting – Commercial &amp; Residential Landscape Lighting</title>
<link rel="stylesheet" href="https://fonts.googleapis.com/css2?family=Montserrat:wght@400;500;600;700;800&display=swap">
<style>
:root{
  --verdant:#59ff00;
  --mint-icon:#dcfcc4;
  --sun:#ffc000;
  --sun-deep:#f5a300;
  --ivory:#fdf2cf;
  --ink:#1f1f1f;
  --text:#4a4a4a;
  --night:#24272c;
  --white:#ffffff;
  --accent-red:#e8262e;
}
*{margin:0;padding:0;box-sizing:border-box}
html,body{width:1200px;height:4324px;overflow:hidden}
body{position:relative;font-family:"Montserrat",sans-serif;color:var(--ink);background:var(--white)}
.abs{position:absolute}

/* header + hero */
.hero{position:absolute;left:0;top:0;width:1200px;height:840px;overflow:hidden}
.hero-photo{position:absolute;inset:0;background:linear-gradient(160deg,#1b2a24 0%,#2d3a26 40%,#4a3a22 60%,#3b5a22 85%,#2f4a1c 100%)}
.hero-shade{position:absolute;inset:0;background:linear-gradient(90deg,rgba(0,0,0,.55) 0%,rgba(0,0,0,.2) 55%,rgba(0,0,0,0) 100%)}
.brand{position:absolute;left:87px;top:34px;width:160px;color:var(--accent-red);font-weight:700;font-size:19px;line-height:1.15;letter-spacing:.5px}
.nav{position:absolute;top:44px;left:296px;list-style:none}
.nav li{color:var(--white);font-size:12px;font-weight:500;white-space:nowrap;position:absolute;top:0}
.btn-contact{position:absolute;left:972px;top:28px;width:137px;height:48px;border-radius:5px;background:var(--sun);color:var(--ink);font-size:12px;font-weight:500;display:flex;align-items:center;justify-content:center}
.hero-copy{position:absolute;left:87px;top:270px;color:var(--white)}
.hero-kicker{font-size:26px;font-weight:400;letter-spacing:.3px}
.hero-title{font-size:55px;font-weight:800;line-height:60px;margin-top:4px}
.hero-sub{font-size:18px;font-weight:700;margin-top:14px}
.hero-text{font-size:14px;line-height:20px;margin-top:12px;width:500px}
.btn-green{display:flex;align-items:center;justify-content:center;background:var(--verdant);color:var(--ink);font-size:11px;font-weight:500;border-radius:5px}
.hero-cta{position:absolute;left:89px;top:515px;width:193px;height:44px}

/* what we do */
.service-photo{position:absolute;left:84px;top:884px;width:570px;height:386px;background:linear-gradient(180deg,#1d2e4a 0%,#3a4a5e 35%,#7a4a2a 60%,#2c3b24 100%)}
.service-card{position:absolute;left:577px;top:923px;width:564px;height:382px;background:var(--white);box-shadow:0 6px 24px rgba(0,0,0,.12);padding:92px 0 0 67px}
.eyebrow{color:var(--sun-deep);font-size:15px;font-weight:500;letter-spacing:.3px}
.h2{font-size:26px;font-weight:600;line-height:32px;color:var(--ink)}
.body{font-size:13px;line-height:19.5px;color:var(--text)}
.ticks{list-style:none;margin-top:10px}
.ticks li{font-size:13px;line-height:19.5px;color:var(--text);display:flex;align-items:center;gap:8px}
.tick{width:11px;height:11px;border-radius:50%;background:#43c51e;flex:none}

/* process */
.process{position:absolute;left:0;top:1410px;width:1200px;height:505px;background:#f0ffdf}
.process-title{position:absolute;top:108px;width:1200px;text-align:center;font-size:24px;font-weight:600}
.step{position:absolute;top:151px;width:250px;height:268px;background:var(--white);box-shadow:0 4px 16px rgba(0,0,0,.06);text-align:center}
.step-icon{width:84px;height:84px;border-radius:50%;background:var(--mint-icon);margin:28px auto 0;display:flex;align-items:center;justify-content:center}
.step-icon.sun{background:var(--sun)}
.step h3{font-size:15px;font-weight:600;line-height:17px;margin-top:14px}
.step p{font-size:13px;line-height:19.5px;color:var(--text);margin:9px 22px 0}

/* about */
.about-copy{position:absolute;left:96px;top:2037px;width:510px}
.about-photo{position:absolute;left:646px;top:2014px;width:456px;height:382px;background:linear-gradient(180deg,#2c3a2c 0%,#56606a 35%,#6b3e26 60%,#2b4320 100%)}
.offers{position:absolute;left:0;top:2357px;width:1200px;height:340px;background:var(--ivory)}
.badge-art{position:absolute;left:148px;top:59px;width:305px;height:227px;border-radius:8px;background:radial-gradient(ellipse at center,#ffd54a 0%,#ffb000 55%,#f08a00 100%)}
.offer-copy{position:absolute;left:567px;top:138px;width:480px}

/* why */
.why{position:absolute;left:0;top:2820px;width:1200px;text-align:center}
.video{position:absolute;left:183px;top:2967px;width:834px;height:384px;background:linear-gradient(180deg,#3a4a3a 0%,#5c6a72 40%,#6b4a2a 62%,#2c4a1e 100%)}
.play{position:absolute;left:368px;top:143px;width:98px;height:98px;border-radius:50%;background:var(--white);display:flex;align-items:center;justify-content:center}

/* testimonials */
.testimonials-title{position:absolute;top:3440px;width:1200px;text-align:center;font-size:24px;font-weight:600}
.track{position:absolute;left:0;width:1200px;height:170px;overflow:hidden}
.review{position:absolute;top:0;width:325px;height:158px;background:var(--white);box-shadow:0 3px 14px rgba(0,0,0,.08);padding:22px 20px 0 20px}
.review-head{display:flex;align-items:center;gap:12px}
.avatar{width:38px;height:38px;border-radius:50%;background:#c9c0b4;flex:none}
.review-name{font-size:13px;font-weight:500}
.stars{color:var(--sun);font-size:10px;letter-spacing:1px}
.quote{position:absolute;right:20px;top:18px;color:#c8c8c8;font-size:36px;font-weight:800;line-height:1}
.review p{font-size:10.5px;line-height:19.5px;color:var(--text);margin-top:12px}
.dots{position:absolute;top:3904px;left:552px;display:flex;gap:14px;align-items:center}
.dot{width:4px;height:4px;border-radius:50%;background:#b5b5b5}
.dot.on{width:14px;height:14px;border:2px solid var(--verdant);background:#fff;position:relative}
.dot.on::after{content:"";position:absolute;left:3px;top:3px;width:4px;height:4px;border-radius:50%;background:var(--verdant)}

/* footer */
.footer{position:absolute;left:0;top:4000px;width:1200px;height:324px}
.footer-brand{position:absolute;top:110px;width:1200px;text-align:center;color:var(--white);font-size:26px;font-weight:600;letter-spacing:1px}
.contact-line{position:absolute;left:124px;color:var(--white);font-size:11px;display:flex;align-items:center;gap:10px}
.contact-line svg{flex:none}
.footer-nav{position:absolute;left:404px;top:218px;display:flex;list-style:none;color:var(--white);font-size:10px;font-weight:500}
.footer-nav li{padding:0 12px;border-left:1px solid rgba(255,255,255,.5);line-height:12px}
.footer-nav li:first-child{border-left:none;padding-left:0}
.social{position:absolute;top:275px;width:34px;height:34px;border-radius:50%;background:#5a5d63}
.social.first{background:var(--verdant)}
.legal{position:absolute;left:732px;top:277px;color:var(--white);font-size:9.5px;display:flex;gap:22px}
</style>
</head>
<body>

<header class="hero">
  <div class="hero-photo" role="img" aria-label="Photo of a brick house at dusk with landscape lighting glowing across the front lawn and shrubs"></div>
  <div class="hero-shade"></div>
  <div class="brand">Corwin Beacon Lighting</div>
  <ul class="nav">
    <li style="left:0;top:-2px"><svg width="16" height="14" viewBox="0 0 16 14"><path d="M8 0 0 7h2v7h4V9h4v5h4V7h2z" fill="#fff"/></svg></li>
    <li style="left:37px">WHAT WE DO</li>
    <li style="left:151px">WHY LIGHTING MATTERS</li>
    <li style="left:330px">OUR PROCESS</li>
    <li style="left:448px">SPECIAL OFFERS</li>
    <li style="left:577px">ABOUT US</li>
  </ul>
  <div class="btn-contact">CONTACT US</div>
  <div class="hero-copy">
    <div class="hero-kicker">WELCOME TO CORWIN</div>
    <h1 class="hero-title">ILLUMINATE WITH<br>CONFIDENCE.</h1>
    <div class="hero-sub">DESIGNED WITH PRECISION. INSTALLED WITH CARE.</div>
    <p class="hero-text">Transform your home or business with breathtaking outdoor lighting — tailored to your vision, installed with expert care.</p>
  </div>
  <div class="btn-green hero-cta">GET YOUR FREE ESTIMATE</div>
  <svg class="abs" style="left:0;top:700px" width="1200" height="140" viewBox="0 0 1200 140">
    <polygon points="0,63 600,13 1200,63 1200,140 0,140" fill="var(--sun)"/>
    <polygon points="0,140 600,25 1200,140" fill="#fff"/>
  </svg>
</header>

<section class="what-we-do">
  <div class="service-photo" role="img" aria-label="Photo of a ranch home at twilight with warm uplights along the front garden"></div>
  <div class="service-card">
    <div class="eyebrow">WHAT WE DO</div>
    <h2 class="h2" style="margin-top:6px">EXPERT OUTDOOR LIGHTING<br>SERVICES THAT MAKE AN IMPACT</h2>
    <p class="body" style="margin-top:10px;width:430px">From elegant landscape lighting to festive holiday displays and permanent architectural installations, we craft lighting solutions that blend beauty, safety, and performance.</p>
    <ul class="ticks">
      <li><span class="tick"></span>Residential &amp; Commercial Projects</li>
      <li><span class="tick"></span>Free In-Home Demonstration Kit</li>
      <li><span class="tick"></span>Veteran-Owned &amp; Operated</li>
      <li><span class="tick"></span>Lifetime Warranty + Quarterly Service Plans</li>
    </ul>
  </div>
</section>

<section class="process">
  <h2 class="process-title">OUR PROCESS – SIMPLE &amp; EFFORTLESS</h2>
  <div class="step" style="left:87px">
    <div class="step-icon"><svg width="40" height="40" viewBox="0 0 40 40" fill="none" stroke="#43c51e" stroke-width="2.5"><path d="M22 8H8v24h24V18"/><path d="M28 6l6 6-14 14h-6v-6z"/></svg></div>
    <h3>FREE ESTIMATE<br>REQUEST</h3>
    <p>Tell us about your property. We'll guide you on the best options.</p>
  </div>
  <div class="step" style="left:346px">
    <div class="step-icon"><svg width="40" height="40" viewBox="0 0 40 40" fill="none" stroke="#43c51e" stroke-width="2.2"><circle cx="20" cy="14" r="8"/><path d="M4 30h8l6 4h12l6-6-6-2-8 2"/></svg></div>
    <h3>ONGOING<br>SUPPORT</h3>
    <p>Enjoy peace of mind with our lifetime warranty and optional quarterly service.</p>
  </div>
  <div class="step" style="left:605px">
    <div class="step-icon sun"><svg width="40" height="40" viewBox="0 0 40 40" fill="none" stroke="#fff" stroke-width="2.5"><circle cx="20" cy="20" r="7"/><path d="M20 4v6M20 30v6M4 20h6M30 20h6M9 9l4 4M27 27l4 4M31 9l-4 4M13 27l-4 4"/></svg></div>
    <h3>CUSTOM DESIGN +<br>INSTALLATION</h3>
    <p>Every project is built around your unique vision and needs.</p>
  </div>
  <div class="step" style="left:864px">
    <div class="step-icon"><svg width="44" height="44" viewBox="0 0 44 44" fill="none" stroke="#43c51e" stroke-width="2"><polygon points="22,4 38,13 38,31 22,40 6,31 6,13"/><text x="22" y="26" font-family="Montserrat,sans-serif" font-size="9" font-weight="700" fill="#43c51e" stroke="none" text-anchor="middle">DEMO</text></svg></div>
    <h3>COMPLIMENTARY<br>DEMO KIT</h3>
    <p>Experience how lighting will transform your space — before spending a dime.</p>
  </div>
</section>

<section class="about">
  <div class="offers">
    <div class="badge-art" role="img" aria-label="Illustrated ribbon badge announcing a 10% discount"></div>
    <div class="offer-copy">
      <h2 class="h2" style="font-weight:600">SPECIAL OFFERS <b style="font-weight:800">10%</b> DISCOUNT</h2>
      <p class="body" style="margin-top:10px;width:470px">For all military personnel, veterans, and first responders — our way of saying thank you.</p>
      <p class="body" style="margin-top:8px;color:var(--ink);font-weight:600">Free Estimates Always Available</p>
    </div>
  </div>
  <div class="about-copy">
    <div class="eyebrow">ABOUT US</div>
    <h2 class="h2" style="margin-top:8px">A VETERAN'S VISION, A FAMILY'S<br>PASSION</h2>
    <p class="body" style="margin-top:10px">Founded by Derek, a retired Army veteran, and his wife Jolene, our company was born out of a love for lighting and a commitment to excellence. After years of lighting homes for friends and family, Derek decided to bring that same level of care to clients across the community.</p>
    <div class="btn-green" style="width:149px;height:43px;margin-top:20px">READ OUR STORY</div>
  </div>
  <svg class="abs" style="left:644px;top:2370px" width="460" height="52" viewBox="0 0 460 52"><polygon points="0,0 460,26 460,40 0,52" fill="var(--sun)"/></svg>
  <div class="about-photo" role="img" aria-label="Photo of a brick home among tall trees with garden lights glowing at dusk"></div>
</section>

<section class="why">
  <div class="eyebrow">WHY LIGHTING MATTERS</div>
  <h2 class="h2" style="margin-top:6px;font-size:25px">LIGHT UP BEAUTY. LIGHT UP SAFETY</h2>
  <p class="body" style="width:720px;margin:6px auto 0">Outdoor lighting doesn't just elevate your curb appeal — it also keeps your loved ones safe. A well-lit home deters intruders and keeps walkways, entrances, and driveways visible and secure at night.</p>
  <p style="font-size:13px;color:var(--sun-deep);font-style:italic;font-weight:500;margin-top:5px">Peace of mind meets visual elegance.</p>
</section>
<div class="video" role="img" aria-label="Video still of a lit home and lawn at nightfall">
  <div class="play"><svg width="26" height="28" viewBox="0 0 26 28"><polygon points="4,2 24,14 4,26" fill="#111"/></svg></div>
</div>

<section class="testimonials">
  <h2 class="testimonials-title">TESTIMONIALS</h2>
  <div class="track" style="top:3520px">
    <article class="review" style="left:-98px"><div class="review-head"><span class="avatar"></span><div><div class="review-name">Marisol Keane</div><div class="stars">★★★★★</div></div></div><span class="quote">“</span><p>Lorem Ipsum is simply dummy text of the printing and typesetting industry. Lorem Ipsum has been the industry's standard dummy text ever since</p></article>
    <article class="review" style="left:252px"><div class="review-head"><span class="avatar"></span><div><div class="review-name">Marisol Keane</div><div class="stars">★★★★★</div></div></div><span class="quote">“</span><p>Lorem Ipsum is simply dummy text of the printing and typesetting industry. Lorem Ipsum has been the industry's standard dummy text ever since</p></article>
    <article class="review" style="left:602px"><div class="review-head"><span class="avatar"></span><div><div class="review-name">Theo Barrett</div><div class="stars">★★★★★</div></div></div><span class="quote">“</span><p>Lorem Ipsum is simply dummy text of the printing and typesetting industry. Lorem Ipsum has been the industry's standard dummy text ever since</p></article>
    <article class="review" style="left:953px"><div class="review-head"><span class="avatar"></span><div><div class="review-name">Owen Pritchard</div><div class="stars">★★★★★</div></div></div><span class="quote">“</span><p>Lorem Ipsum is simply dummy text of the printing and typesetting industry. Lorem Ipsum has been the industry's standard dummy text ever since</p></article>
  </div>
  <div class="track" style="top:3698px">
    <article class="review" style="left:-73px"><div class="review-head"><span class="avatar"></span><div><div class="review-name">Marisol Keane</div><div class="stars">★★★★★</div></div></div><span class="quote">“</span><p>Lorem Ipsum is simply dummy text of the printing and typesetting industry. Lorem Ipsum has been the industry's standard dummy text ever since</p></article>
    <article class="review" style="left:275px"><div class="review-head"><span class="avatar"></span><div><div class="review-name">Nadia Fell</div><div class="stars">★★★★★</div></div></div><span class="quote">“</span><p>Lorem Ipsum is simply dummy text of the printing and typesetting industry. Lorem Ipsum has been the industry's standard dummy text ever since</p></article>
    <article class="review" style="left:623px"><div class="review-head"><span class="avatar"></span><div><div class="review-name">Lena Orwell</div><div class="stars">★★★★★</div></div></div><span class="quote">“</span><p>Lorem Ipsum is simply dummy text of the printing and typesetting industry. Lorem Ipsum has been the industry's standard dummy text ever since</p></article>
    <article class="review" style="left:973px"><div class="review-head"><span class="avatar"></span><div><div class="review-name">Priya Castell</div><div class="stars">★★★★★</div></div></div><span class="quote">“</span><p>Lorem Ipsum is simply dummy text of the printing and typesetting industry. Lorem Ipsum has been the industry's standard dummy text ever since</p></article>
  </div>
  <div class="dots"><span class="dot"></span><span class="dot"></span><span class="dot on"></span><span class="dot"></span><span class="dot"></span></div>
</section>

<footer class="footer">
  <svg class="abs" style="left:0;top:0" width="1200" height="324" viewBox="0 0 1200 324">
    <polygon points="0,57 600,10 1200,57 1200,324 0,324" fill="var(--sun)"/>
    <polygon points="0,108 600,52 1200,108 1200,324 0,324" fill="var(--night)"/>
  </svg>
  <div class="footer-brand">Corwin Beacon Lighting</div>
  <div class="contact-line" style="top:196px"><svg width="12" height="12" viewBox="0 0 12 12"><path d="M2 1l2 0 1 3-1.5 1a7 7 0 0 0 3.5 3.5L8 7l3 1v2a1 1 0 0 1-1 1A9 9 0 0 1 1 2a1 1 0 0 1 1-1z" fill="var(--sun)"/></svg>(555)018-2740</div>
  <div class="contact-line" style="top:220px"><svg width="12" height="10" viewBox="0 0 12 10"><rect width="12" height="10" rx="1" fill="var(--sun)"/><path d="M0 1l6 5 6-5" stroke="var(--night)" fill="none"/></svg>hello@corwinbeacon.example</div>
  <ul class="footer-nav">
    <li>HOME</li><li>WHAT WE DO</li><li>WHY LIGHTING MATTERS</li><li>OUR PROCESS</li><li>SPECIAL OFFERS</li><li>ABOUT US</li><li>CONTACT US</li>
  </ul>
  <span class="social first" style="left:114px"></span>
  <span class="social" style="left:159px"></span>
  <span class="social" style="left:199px"></span>
  <span class="social" style="left:240px"></span>
  <div class="legal"><span>© 2025. All rights reserved.</span><span>Terms of Service</span><span>Privacy and Cookies</span></div>
</footer>

</body>
</html>
```